FinTech company looking to revamp and expand client-facing interface for our financial models

Pellworth Engines currently has a very simple website that allows clients to interact with our financial models. We are looking to completely redesign the current site and add several extra pages to provide extra functionality. We want the design to have a modern, slick feel, that will work on both a desktop or a tablet. It should be straightforward for clients to move between different pages at any time, and clear from the layout how to interact with the more advanced features. We have included screenshots of existing pages in the attached design brief, as well as sketches of the functionality required by the new pages, but can't provide a direct link to the current site.
Target Market(s)
Professional investors that will be paying to access the interface
Industry/Entity Type
Finance
Number of Pages Required
4 page
Colors
Designer to choose colors to be used in the design.
Look and feel
Each slider illustrates characteristics of the customer's brand and the style your logo design should communicate.

```html
<!DOCTYPE html>
<html lang="en">
<head>
<meta charset="utf-8">
<title>Pellworth Engines – Models</title>
<link href="https://fonts.googleapis.com/css2?family=Open+Sans:wght@400;600;700&display=swap" rel="stylesheet">
<style>
:root{
  --bar:#8a8a8a;
  --tab-active:#4a86c6;
  --head:#3d6fa8;
  --side:#3a6aa6;
  --row-hi:#3f70ad;
  --line:#c9c9c9;
  --ink:#333;
  --muted:#555;
  --white:#fff;
}
*{box-sizing:border-box;margin:0;padding:0}
html,body{width:1200px;height:1025px;overflow:hidden;background:var(--white);font-family:"Open Sans",sans-serif;color:var(--ink)}
.screen{position:absolute;left:32px;width:1136px;background:var(--white);border:1px solid #d0d0d0;box-shadow:0 1px 3px rgba(0,0,0,.25)}
.topbar{position:absolute;left:0;top:0;width:100%;background:var(--bar);color:var(--white)}
.brand{position:absolute;left:50%;transform:translateX(-50%);font-weight:700;letter-spacing:1px;white-space:nowrap}
.tab{position:absolute;top:0;height:100%;display:flex;align-items:center;justify-content:center;font-size:17px}
.tab.active{background:var(--tab-active)}
.nav{position:absolute;top:0;height:100%;display:flex;align-items:center;font-size:14px;font-weight:600;text-transform:uppercase;gap:3px}
.nav svg{width:13px;height:13px;fill:var(--white)}
.field-label{position:absolute;font-size:14px;white-space:nowrap}
.field{position:absolute;height:24px;border:1px solid #bdbdbd;font-size:14px;padding-left:8px;line-height:22px;color:var(--ink)}
.export{position:absolute;font-size:12.5px;color:var(--muted);display:flex;align-items:center;gap:3px}
.export svg{width:12px;height:12px;fill:none;stroke:var(--head);stroke-width:1.6}
table{position:absolute;border-collapse:collapse;table-layout:fixed}
th{background:var(--head);color:var(--white);font-weight:600;border:1px solid #5a86bb}
td{border:1px solid var(--line);text-align:center}
.data th{height:30px;font-size:13px}
.data td{height:44.5px;font-size:12.5px;color:var(--muted);line-height:1.45}
.data td.id{background:var(--tab-active);color:var(--white);font-weight:600;border-color:#6a9bd0}
.data td.sector{color:#222;font-weight:600;font-size:12.5px;line-height:1.3}
.data tr.hi td{background:var(--row-hi);color:var(--white);border-color:#5a86bb}
.factors th{height:32px;font-size:14.5px}
.factors td{height:34px;font-size:14px;color:#222}
.copyright{position:absolute;left:0;width:1200px;text-align:center;font-size:14px;color:var(--muted)}
.sidebar{position:absolute;left:0;top:47px;width:175px;bottom:0;background:var(--side)}
.side-item{position:absolute;left:0;width:175px;color:var(--white);font-size:16px;padding-left:57px;height:47px;line-height:47px}
.side-item.active{background:var(--white);color:#222}
.dropdown{position:absolute;left:770px;top:47px;width:98px;height:129px;background:var(--white);border:1px solid #ccc;box-shadow:0 2px 3px rgba(0,0,0,.2)}
.dropdown span{position:absolute;left:12px;font-size:12.5px;color:var(--muted)}
</style>
</head>
<body>

<section class="screen" style="top:29px;height:411px">
  <header class="topbar" style="height:52px">
    <div class="tab" style="left:22px;width:58px;font-size:20px">QMETRIC</div>
    <div class="tab active" style="left:129px;width:59px">250D</div>
    <div class="tab" style="left:199px;width:40px">83D</div>
    <div class="tab" style="left:257px;width:40px">42D</div>
    <div class="brand" style="top:6px;font-size:30px">PELLWORTH ENGINES</div>
    <div class="nav" style="left:782px"><svg viewBox="0 0 16 16"><path d="M8 1 0 8h2v7h4v-5h4v5h4V8h2z"/></svg>Models</div>
    <div class="nav" style="left:878px"><svg viewBox="0 0 16 16"><path d="M7 0h2l.4 2.2 1.4.6 1.9-1.3 1.4 1.4-1.3 1.9.6 1.4L16 7v2l-2.2.4-.6 1.4 1.3 1.9-1.4 1.4-1.9-1.3-1.4.6L9 16H7l-.4-2.2-1.4-.6-1.9 1.3-1.4-1.4 1.3-1.9-.6-1.4L0 9V7l2.2-.4.6-1.4-1.3-1.9 1.4-1.4 1.9 1.3 1.4-.6zM8 5a3 3 0 1 0 0 6 3 3 0 0 0 0-6z"/></svg>Sensitivities</div>
    <div class="nav" style="left:1010px"><svg viewBox="0 0 16 16"><path d="m8 0 2.4 5.2 5.6.6-4.2 3.8 1.2 5.6L8 12.4 3 15.2l1.2-5.6L0 5.8l5.6-.6z"/></svg>Favorites</div>
  </header>

  <div class="field-label" style="left:30px;top:72px"><span style="font-size:12.5px;color:var(--muted)">Quality</span>&nbsp; <b style="font-weight:600">THRESHOLD</b></div>
  <div class="field" style="left:174px;top:70px;width:182px">-10</div>
  <div class="field-label" style="left:376px;top:72px"><b style="font-weight:600">ABS.</b> <span style="font-size:12.5px;color:var(--muted)">Stat</span>&nbsp; <b style="font-weight:600">THRESHOLD</b></div>
  <div class="field" style="left:538px;top:70px;width:182px">-10</div>
  <div class="export" style="left:34px;top:106px"><svg viewBox="0 0 12 12"><path d="M9 7v4H1V3h4M7 1h4v4M11 1 5 7"/></svg>Export</div>

  <table class="data" style="left:30px;top:139px;width:1076px">
    <colgroup><col style="width:82px"><col style="width:90px"><col style="width:90px"><col span="9" style="width:90.4px"></colgroup>
    <thead><tr><th>ID ▾</th><th>SECTOR</th><th>TIME</th><th>QUALITY</th><th>STAT 1</th><th>STAT 2</th><th>STAT 3</th><th>STAT 4</th><th>STAT 5</th><th>STAT 6</th><th>STAT 7</th><th>STAT 8</th></tr></thead>
    <tbody>
      <tr><td class="id">MODEL 1</td><td class="sector">Materials</td><td>2019-07-03<br>12:15:00.000</td><td>30.2288</td><td>2.01574</td><td>23.305</td><td>-0.149368</td><td>22.3054</td><td>4.63714</td><td>0.945706</td><td>2.81949</td><td>2.60858</td></tr>
      <tr><td class="id">MODEL 1</td><td class="sector">Industrials</td><td>2019-07-03<br>12:15:00.000</td><td>32.8694</td><td>0.87307</td><td>32.185</td><td>-0.0336927</td><td>33.9911</td><td>11.5693</td><td>-0.472968</td><td>-0.830458</td><td>6.80646</td></tr>
      <tr class="hi"><td class="id">MODEL 1</td><td class="sector">Consumer Discretionary</td><td>2019-07-03<br>12:15:00.000</td><td>30.2288</td><td>-0.569222</td><td>159.814</td><td>0.0252328</td><td>172.616</td><td>10.2875</td><td>-0.750396</td><td>-0.385309</td><td>4.69146</td></tr>
      <tr><td class="id">MODEL 1</td><td class="sector">Information Technology</td><td>2019-07-03<br>12:15:00.000</td><td>45.6856</td><td>0.412148</td><td>202.488</td><td>0.00849232</td><td>205.834</td><td>11.9094</td><td>-0.137913</td><td>0.449595</td><td>3.85106</td></tr>
      <tr><td class="id">MODEL 1</td><td class="sector">Information Technology</td><td>2019-07-03<br>12:15:00.000</td><td>75.7733</td><td>7.06728</td><td>188.605</td><td>0.016913</td><td>181.665</td><td>3.82241</td><td>0.981019</td><td>1.29847</td><td>3.34927</td></tr>
    </tbody>
  </table>
</section>
<p class="copyright" style="top:452px">Copyright © 2019. All Rights Reserved</p>

<section class="screen" style="top:496px;height:461px">
  <header class="topbar" style="height:47px">
    <div class="tab" style="left:55px;width:80px;font-size:20px">FACTORS</div>
    <div class="brand" style="top:3px;font-size:30px">PELLWORTH ENGINES</div>
    <div class="tab active nav" style="left:770px;width:98px;justify-content:center;font-size:14px"><svg viewBox="0 0 16 16"><path d="M8 1 0 8h2v7h4v-5h4v5h4V8h2z"/></svg>Models</div>
    <div class="nav" style="left:874px"><svg viewBox="0 0 16 16"><path d="M7 0h2l.4 2.2 1.4.6 1.9-1.3 1.4 1.4-1.3 1.9.6 1.4L16 7v2l-2.2.4-.6 1.4 1.3 1.9-1.4 1.4-1.9-1.3-1.4.6L9 16H7l-.4-2.2-1.4-.6-1.9 1.3-1.4-1.4 1.3-1.9-.6-1.4L0 9V7l2.2-.4.6-1.4-1.3-1.9 1.4-1.4 1.9 1.3 1.4-.6zM8 5a3 3 0 1 0 0 6 3 3 0 0 0 0-6z"/></svg>Sensitivities</div>
    <div class="nav" style="left:1002px"><svg viewBox="0 0 16 16"><path d="m8 0 2.4 5.2 5.6.6-4.2 3.8 1.2 5.6L8 12.4 3 15.2l1.2-5.6L0 5.8l5.6-.6z"/></svg>Favorites</div>
  </header>

  <aside class="sidebar">
    <div class="side-item active" style="top:1px">250D</div>
    <svg style="position:absolute;left:157px;top:1px" width="18" height="47" viewBox="0 0 18 47"><path d="M18 0 0 23.5 18 47z" fill="var(--side)"/></svg>
    <div class="side-item" style="top:46px">83D</div>
    <div class="side-item" style="top:91px">42D</div>
  </aside>

  <div class="field-label" style="left:183px;top:73px;font-size:15px;font-weight:600">Stat 1 Threshould</div>
  <div class="field" style="left:325px;top:71px;width:178px">-10</div>
  <div class="field-label" style="left:183px;top:113px;font-size:15px;font-weight:600">Stat 2 Threshould</div>
  <div class="field" style="left:325px;top:111px;width:178px">-10</div>
  <div class="field-label" style="left:183px;top:151px;font-size:15px;font-weight:600">Stat 3 Threshould</div>
  <div class="field" style="left:325px;top:149px;width:178px">-10</div>

  <div class="dropdown">
    <span style="top:4px">EQUITIES</span>
    <span style="top:29px">ETFS</span>
    <span style="top:54px">PAIRS</span>
    <span style="top:79px">ETF PAIRS</span>
    <span style="top:104px">FACTORS</span>
  </div>

  <div class="export" style="left:183px;top:200px"><svg viewBox="0 0 12 12"><path d="M9 7v4H1V3h4M7 1h4v4M11 1 5 7"/></svg>Export</div>

  <table class="factors" style="left:177px;top:230px;width:924px">
    <colgroup><col span="9" style="width:102.7px"></colgroup>
    <thead><tr><th>FACTOR</th><th>ID</th><th>SECTOR</th><th>STAT 1</th><th>STAT 2</th><th>STAT 3</th><th>STAT 4</th><th>STAT 5</th><th>STAT 6</th></tr></thead>
    <tbody>
      <tr><td>FACTOR</td><td>Model 1</td><td>Materials</td><td>-1.4</td><td>0.1</td><td>-3.1</td><td>0.7</td><td>30.2</td><td>0.9</td></tr>
      <tr><td>FACTOR</td><td>Model 1</td><td>Materials</td><td>2.8</td><td>0.1</td><td>6.1</td><td>100</td><td>30.2</td><td>0.9</td></tr>
      <tr><td>FACTOR</td><td>Model 1</td><td>Materials</td><td>-3.7</td><td>2.7</td><td>-7.2</td><td>100</td><td>30.2</td><td>0.9</td></tr>
      <tr><td>FACTOR</td><td>Model 2</td><td>Industrials</td><td>2.8</td><td>0.2</td><td>2.7</td><td>0.5</td><td>32.9</td><td>-0.5</td></tr>
      <tr><td>FACTOR</td><td>Model 1</td><td>Industrials</td><td>0.8</td><td>0.3</td><td>2.5</td><td>0.5</td><td>32.9</td><td>-0.5</td></tr>
    </tbody>
  </table>
</section>
<p class="copyright" style="top:981px">Copyright © 2019. All Rights Reserved</p>

</body>
</html>
```